Corvane Capital Business Cards

These are professional business cards that are for my family office.
Put fake emails and phone numbers as of now until I finalize those components. This family office controls my families investments, assets, and future. The cards should be professional.
..
.
.
.
I just uploaded another variation of a logo I would like to see as a business card to I am inbeteen which logo to use

Target Market(s)

business

Industry/Entity Type

business

Contact Information for Business Card

Professional, wealth related, finance related.

Requirements
Must have
• Logo

```html
<!DOCTYPE html>
<html lang="en">
<head>
<meta charset="UTF-8">
<title>Corvane Capital Business Cards</title>
<link rel="stylesheet" href="https://fonts.googleapis.com/css2?family=Cinzel:wght@500&family=Montserrat:wght@400;700&display=swap">
<style>
  :root {
    --backdrop: #3a3a3c;
    --navy: #1c2233;
    --navy-deep: #151a28;
    --accent-blue: #4a5da8;
    --ink: #1d2236;
    --paper: #ffffff;
    --silver: #c9cbd1;
    --muted: #3b4055;
  }
  * { margin: 0; padding: 0; box-sizing: border-box; }
  html, body { width: 1200px; height: 875px; overflow: hidden; }
  body {
    background: var(--backdrop);
    position: relative;
    font-family: "Montserrat", sans-serif;
  }
  .card {
    position: absolute;
    width: 520px;
    height: 298px;
    border-radius: 22px;
    overflow: hidden;
    box-shadow: 0 18px 40px rgba(0,0,0,0.45);
  }
  /* Front side */
  .card-front {
    left: 60px;
    top: 150px;
    background: linear-gradient(135deg, var(--navy) 0%, var(--navy-deep) 100%);
  }
  .front-brand {
    position: absolute;
    left: 46px;
    bottom: 82px;
    display: flex;
    align-items: center;
    gap: 14px;
  }
  .front-mark {
    width: 14px;
    height: 14px;
    background: var(--accent-blue);
    flex-shrink: 0;
  }
  .front-wordmark {
    font-family: "Cinzel", serif;
    font-weight: 500;
    font-size: 32px;
    letter-spacing: 1px;
    color: var(--paper);
    white-space: nowrap;
  }
  .front-web {
    position: absolute;
    left: 48px;
    bottom: 46px;
    font-family: "Montserrat", sans-serif;
    font-weight: 700;
    font-size: 16px;
    color: var(--silver);
  }
  /* Back side */
  .card-back {
    left: 620px;
    top: 430px;
    background: var(--paper);
  }
  .back-brand {
    position: absolute;
    left: 22px;
    top: 0;
    width: 226px;
    height: 100%;
    display: flex;
    align-items: center;
    justify-content: center;
    gap: 10px;
  }
  .brand-mark {
    width: 10px;
    height: 10px;
    background: var(--ink);
    flex-shrink: 0;
  }
  .back-wordmark {
    font-family: "Cinzel", serif;
    font-weight: 500;
    font-size: 19px;
    color: var(--ink);
    white-space: nowrap;
  }
  .divider {
    position: absolute;
    left: 258px;
    top: 52px;
    width: 1.5px;
    height: 194px;
    background: var(--ink);
  }
  .details {
    position: absolute;
    left: 280px;
    top: 50px;
    color: var(--ink);
  }
  .person-name { font-weight: 700; font-size: 21px; line-height: 1.1; }
  .person-role { font-size: 12px; color: var(--muted); margin-bottom: 14px; }
  .address { font-size: 11.5px; line-height: 1.35; color: var(--muted); margin-bottom: 14px; }
  .contact-list { list-style: none; font-size: 11.5px; color: var(--muted); }
  .contact-list li { display: flex; align-items: center; gap: 8px; margin-bottom: 6px; }
  .contact-list svg { width: 11px; height: 11px; fill: var(--ink); flex-shrink: 0; }
</style>
</head>
<body>

<section class="card card-front" aria-label="Card front">
  <div class="front-brand">
    <div class="front-mark"></div>
    <div class="front-wordmark">Corvane Capital</div>
  </div>
  <div class="front-web">www.corvanecapital.com</div>
</section>

<section class="card card-back" aria-label="Card back">
  <div class="back-brand">
    <div class="brand-mark"></div>
    <div class="back-wordmark">Corvane Capital</div>
  </div>
  <div class="divider"></div>
  <div class="details">
    <div class="person-name">Martin Ellery</div>
    <div class="person-role">Owner</div>
    <div class="address">48 Harbor Point Lane<br>Fairlow, NJ 07412 USA</div>
    <ul class="contact-list">
      <li>
        <svg viewBox="0 0 24 24" aria-hidden="true"><path d="M6.6 10.8a15 15 0 0 0 6.6 6.6l2.2-2.2a1 1 0 0 1 1-.25 11.4 11.4 0 0 0 3.6.57 1 1 0 0 1 1 1V20a1 1 0 0 1-1 1A17 17 0 0 1 3 4a1 1 0 0 1 1-1h3.5a1 1 0 0 1 1 1c0 1.25.2 2.45.57 3.6a1 1 0 0 1-.25 1z"/></svg>
        (555) 214-7730
      </li>
      <li>
        <svg viewBox="0 0 24 24" aria-hidden="true"><path d="M2 5h20v14H2z M2 5l10 8 10-8" /></svg>
        info@corvanecapital.com
      </li>
      <li>
        <svg viewBox="0 0 24 24" aria-hidden="true"><circle cx="12" cy="12" r="10"/></svg>
        www.corvanecapital.com
      </li>
    </ul>
  </div>
</section>

</body>
</html>
```